32 x 24 Swinging Real Estate Yard Sign

We are looking to design a new sign for our business to focus on the remodeling of homes to sell. We are looking to have a yard sign that gets peoples attention and is informational. The headline will be "The Secret to Top Dollar? Remodel First.". We remodel homes for sellers with no up front cost, as they simply pay at closing. This link has more info, https://bramblecresthomes.com/Remodel
The message we want to convey to those seeing the sign is we are a one stop shop, who can renovate your home and sell it for no stress. We are licensed real estate agents and licensed contractors.
Both of these license numbers and info need to be on the design:
CADRE #02794613
Contractors License #1178524
Email: info@bramblecresthomes.com
Phone: (408)614-2907
I'll attach a sample sign we have for our agents normally as well as all brand art work.
• Pantone Colors
o #172A41
Dark blue
o #4381B1
Medium blue
o #6FA6CC
Light blue
Target Market(s)
Residential Real Estate Sellers
Industry/Entity Type
Real Estate
Colors
Designer to choose colors to be used in the design.

```html
<!DOCTYPE html>
<html lang="en">
<head>
<meta charset="utf-8">
<title>Bramblecrest Homes – Remodel First Yard Sign</title>
<link rel="stylesheet" href="https://fonts.googleapis.com/css2?family=Poppins:wght@400;500;600;700;800;900&display=swap">
<style>
  :root {
    --dark-blue: #172A41;
    --medium-blue: #4381B1;
    --light-blue: #6FA6CC;
    --white: #FFFFFF;
    --visual-top: #D9C9A0;
    --visual-bottom: #E6E9EE;
    --cloud: #C9D3DE;
  }
  * { box-sizing: border-box; margin: 0; padding: 0; }
  html, body {
    width: 916px;
    height: 1200px;
    overflow: hidden;
    background: var(--white);
    font-family: "Poppins", sans-serif;
  }
  .sign {
    position: relative;
    width: 916px;
    height: 1200px;
    overflow: hidden;
    background: var(--white);
  }
  .sky {
    position: absolute;
    left: 0; top: 0;
    width: 916px; height: 851px;
    background:
      radial-gradient(circle at 100% 0%, rgba(67,129,177,0.95) 0, rgba(67,129,177,0.35) 140px, rgba(23,42,65,0) 300px),
      var(--dark-blue);
  }
  .contact-band {
    position: absolute;
    left: 0; top: 851px;
    width: 916px; height: 208px;
    background: var(--medium-blue);
  }
  .cloud {
    position: absolute;
    border-radius: 10px;
    background: linear-gradient(180deg, rgba(201,211,222,0.35), rgba(201,211,222,0.15));
  }
  .cloud--left { left: 0; top: 106px; width: 165px; height: 105px; }
  .cloud--right { left: 808px; top: 367px; width: 108px; height: 191px; }

  .brand {
    position: absolute;
    left: 0; top: 48px;
    width: 916px;
    display: flex;
    justify-content: center;
    align-items: center;
    gap: 14px;
  }
  .brand__mark {
    width: 22px; height: 22px;
    border-radius: 50%;
    background: var(--light-blue);
  }
  .brand__name {
    font-weight: 600;
    font-size: 38px;
    letter-spacing: 1px;
    color: var(--white);
    line-height: 1;
  }

  .headline {
    position: absolute;
    left: 0; top: 178px;
    width: 916px;
    text-align: center;
    text-transform: uppercase;
    line-height: 1;
    z-index: 2;
  }
  .headline__intro {
    display: block;
    font-size: 38px;
    font-weight: 400;
    color: var(--white);
    letter-spacing: -0.5px;
  }
  .headline__intro strong { font-weight: 800; }
  .headline__question {
    display: block;
    margin-top: 14px;
    font-size: 68px;
    font-weight: 800;
    color: var(--white);
    letter-spacing: -2px;
  }
  .headline__question .accent { color: var(--medium-blue); }
  .headline__remodel {
    display: block;
    margin-top: 6px;
    font-size: 120px;
    font-weight: 800;
    color: var(--medium-blue);
    letter-spacing: -4px;
  }
  .headline__first {
    display: block;
    margin-top: -6px;
    font-size: 206px;
    font-weight: 800;
    color: var(--white);
    letter-spacing: -6px;
  }

  .house-visual {
    position: absolute;
    left: 100px; top: 598px;
    width: 740px; height: 336px;
    border-radius: 12px;
    background: linear-gradient(180deg, var(--visual-top) 0%, var(--visual-bottom) 100%);
    z-index: 1;
  }

  .phone {
    position: absolute;
    left: 0; top: 962px;
    width: 916px;
    display: flex;
    justify-content: center;
    align-items: center;
    gap: 8px;
  }
  .phone__icon {
    width: 74px; height: 74px;
    border-radius: 50%;
    background: var(--dark-blue);
    display: flex;
    align-items: center;
    justify-content: center;
  }
  .phone__number {
    font-size: 78px;
    font-weight: 700;
    color: var(--white);
    letter-spacing: -1px;
    line-height: 1;
  }

  .email {
    position: absolute;
    left: 0; top: 1073px;
    width: 916px;
    display: flex;
    justify-content: center;
    align-items: center;
    gap: 18px;
  }
  .email__address {
    font-size: 36px;
    font-weight: 600;
    color: var(--dark-blue);
    line-height: 1;
  }

  .licenses {
    position: absolute;
    left: 0; top: 1136px;
    width: 916px;
    display: flex;
    justify-content: center;
    gap: 5px;
  }
  .license {
    display: flex;
    height: 34px;
    border-radius: 17px;
    overflow: hidden;
    font-size: 18px;
    font-weight: 700;
    line-height: 34px;
    color: var(--white);
  }
  .license__label { background: var(--dark-blue); padding: 0 12px 0 16px; }
  .license__number { background: var(--medium-blue); padding: 0 16px 0 12px; }
</style>
</head>
<body>
  <main class="sign">
    <div class="sky"></div>
    <div class="contact-band"></div>

    <div class="cloud cloud--left" role="img" aria-label="Photo of white clouds"></div>
    <div class="cloud cloud--right" role="img" aria-label="Photo of white clouds"></div>

    <header class="brand">
      <span class="brand__mark"></span>
      <span class="brand__name">Bramblecrest Homes</span>
    </header>

    <h1 class="headline">
      <span class="headline__intro">The <strong>Secret</strong> to</span>
      <span class="headline__question"><span class="accent">Top</span> Dollar?</span>
      <span class="headline__remodel">Remodel</span>
      <span class="headline__first">First</span>
    </h1>

    <div class="house-visual" role="img" aria-label="Image of a two-storey cream house with brown roof and trees standing on rolled-out architectural blueprints with pencils"></div>

    <div class="phone">
      <span class="phone__icon">
        <svg width="44" height="44" viewBox="0 0 24 24" aria-hidden="true">
          <path fill="#FFFFFF" d="M6.6 10.8c1.4 2.8 3.8 5.1 6.6 6.6l2.2-2.2c.3-.3.7-.4 1-.2 1.1.4 2.3.6 3.6.6.6 0 1 .4 1 1V20c0 .6-.4 1-1 1C10.6 21 3 13.4 3 4c0-.6.4-1 1-1h3.5c.6 0 1 .4 1 1 0 1.3.2 2.5.6 3.6.1.3 0 .7-.2 1L6.6 10.8z"/>
          <path fill="none" stroke="#FFFFFF" stroke-width="1.6" stroke-linecap="round" d="M14.5 3.5a6 6 0 0 1 6 6M14.5 6.5a3 3 0 0 1 3 3"/>
        </svg>
      </span>
      <span class="phone__number">(408)614-2907</span>
    </div>

    <div class="email">
      <svg width="36" height="26" viewBox="0 0 36 26" aria-hidden="true">
        <rect x="1" y="1" width="34" height="24" fill="#4381B1"/>
        <path d="M1 1 L18 15 L35 1" fill="none" stroke="#FFFFFF" stroke-width="2"/>
        <path d="M1 25 L13 11 M35 25 L23 11" stroke="#FFFFFF" stroke-width="1.5"/>
      </svg>
      <span class="email__address">info@bramblecresthomes.com</span>
    </div>

    <div class="licenses">
      <div class="license">
        <span class="license__label">CADRE</span>
        <span class="license__number">#02794613</span>
      </div>
      <div class="license">
        <span class="license__label">CONTRACTORS LICENSE</span>
        <span class="license__number">#1178524</span>
      </div>
    </div>
  </main>
</body>
</html>
```